New Website for novelty yarn producer

We need a new website for our company, Vedrana. We make highly tailored yarns for weavers worldwide. This year marks our 40th anniversary and we want to evolve our image and identity.

Our temporary website can be found at:
www.vedranathreads.example

Our only concern in that throughout the website the protagonist must be our client, we make their creations possible and are highly adaptable both during the ideation process of the yarn as well as in the production. This is at the core of the way we do business and is summarised within the concept of FMC (Full Motion Craft).

Industry/Entity Type

Textile

Number of Pages Required

1 page

Colors
9bcb3c

Requirements
Must have
• Full Motion Craft (FMC) - can be found on or current website www.vedranathreads.example

```html
<!DOCTYPE html>
<html lang="en">
<head>
<meta charset="utf-8">
<title>Vedrana Novelty Yarn Solutions</title>
<link href="https://fonts.googleapis.com/css2?family=Lora:wght@400;700&family=Open+Sans:wght@400;600;700&display=swap" rel="stylesheet">
<style>
:root{
  --green:#9bcb3c;
  --green-dark:#86b52c;
  --ink:#1d1d1d;
  --text:#444;
  --white:#fff;
  --light:#efefef;
  --placeholder:#ececec;
}
*{margin:0;padding:0;box-sizing:border-box}
html,body{width:1200px;height:3025px;overflow:hidden}
body{font-family:'Open Sans',sans-serif;color:var(--text);background:var(--white);position:relative}
a{text-decoration:none}
.wordmark{font-family:'Lora',serif;font-weight:700;color:var(--ink);font-size:50px;letter-spacing:1px;line-height:1}
.btn{display:inline-block;font-family:'Open Sans',sans-serif;font-weight:700;font-size:15px;text-align:center;text-decoration:none}
.btn-white{background:var(--white);color:var(--green-dark);width:138px;height:42px;line-height:42px}
.btn-green{background:var(--green);color:var(--white);width:172px;height:42px;line-height:42px}
.dot{display:inline-block;width:18px;height:18px;border-radius:50%;background:currentColor}

/* header */
.site-header{position:absolute;top:0;left:0;width:1200px;height:118px}
.site-header .wordmark{position:absolute;left:75px;top:34px}
.social{position:absolute;display:flex;gap:18px;color:var(--ink)}
.site-header .social{left:756px;top:50px}
.call{position:absolute;left:948px;top:38px;display:flex;align-items:center;gap:14px}
.call-icon{width:34px;height:34px;border-radius:50%;background:var(--green);display:flex;align-items:center;justify-content:center}
.call small{display:block;font-size:14px;color:var(--ink)}
.call strong{display:block;font-size:20px;color:var(--green);font-weight:700}

.main-nav{position:absolute;top:118px;left:0;width:1200px;height:57px;background:var(--green);display:flex;padding-left:75px}
.main-nav a{color:var(--white);font-size:16px;font-weight:600;line-height:57px;padding:0 24px}
.main-nav a.active{background:var(--white);color:var(--green)}
.main-nav a:nth-child(2){margin-left:16px}
.main-nav a:nth-child(3){margin-left:20px}
.main-nav a:nth-child(4){margin-left:20px}

/* hero */
.hero{position:absolute;top:175px;left:0;width:1200px;height:497px;background:linear-gradient(135deg,#3f9a2c,#5cb83a 45%,#3b8d28);text-align:center;color:var(--white)}
.hero h1{font-family:'Lora',serif;font-weight:400;font-size:48px;letter-spacing:1px;margin-top:130px}
.badge{position:absolute;left:515px;top:230px;width:170px;height:170px;border:2px solid rgba(255,255,255,.8);border-radius:50%}
.badge span{display:block;font-family:'Lora',serif;font-size:72px;line-height:1;margin-top:34px}
.badge em{font-style:normal;font-family:'Lora',serif;font-size:18px}
.hero-arrows{position:absolute;left:562px;top:425px}

/* features */
.features{position:absolute;top:672px;left:0;width:1200px;height:423px;background:var(--green);color:var(--white);display:flex;justify-content:center}
.feature{width:354px;text-align:center;position:relative}
.feature svg{margin-top:40px}
.feature h2{font-family:'Lora',serif;font-weight:700;font-size:28px;margin-top:6px}
.feature p{font-size:14.5px;line-height:22px;margin:18px auto 0;width:318px}
.feature .btn{position:absolute;left:108px}

/* approach */
.approach{position:absolute;top:1095px;left:0;width:1200px;height:473px;text-align:center}
.section-title{font-family:'Lora',serif;font-weight:700;font-size:30px;color:var(--ink);letter-spacing:.5px}
.approach .section-title{margin-top:60px}
.concept-mark{width:340px;height:130px;margin:40px auto 0;background:var(--placeholder)}
.approach .lead{font-size:15.5px;line-height:26px;color:var(--ink);margin-top:52px}
.approach .btn{margin-top:28px}

/* team */
.team{position:absolute;top:1568px;left:0;width:1200px;height:424px;background:radial-gradient(circle at 530px 80px,#f2eaa0 0,#efefef 120px),radial-gradient(circle at 700px 370px,#f1d5e2 0,transparent 110px),var(--light);text-align:center;color:#4a4a4a}
.team p{font-size:16.5px;line-height:24px}
.team .p1{margin-top:103px}
.team .p2,.team .p3{margin-top:24px}
.team .btn{margin-top:14px}

/* numbers */
.numbers{position:absolute;top:1992px;left:0;width:1200px;height:398px;background:linear-gradient(180deg,#d9d9d6,#e4e3dc 60%,#ecebe4);text-align:center}
.numbers .section-title{margin-top:30px}
.stats{display:flex;justify-content:space-between;width:1040px;margin:46px auto 0}
.stat{width:300px}
.stat b{display:block;font-size:64px;font-weight:600;color:var(--green);line-height:1}
.stat span{display:block;font-size:16.5px;font-weight:600;color:var(--green);margin-top:20px;letter-spacing:.3px}
.numbers .btn{margin-top:36px}

/* testimonials */
.testimonials{position:absolute;top:2390px;left:0;width:1200px;height:302px;background:linear-gradient(180deg,#3a3a3a,#262626);text-align:center;color:var(--white)}
.testimonials .section-title{color:var(--white);margin-top:34px;line-height:40px}
.quote-mark{font-family:'Lora',serif;font-size:72px;line-height:72px;height:36px;overflow:hidden;color:#bdbdbd;margin-top:6px}
.testimonials p{font-size:16.5px;line-height:28px;width:880px;margin:12px auto 0;color:#eee}
.testimonials cite{display:block;font-style:normal;font-weight:700;font-size:20px;margin-top:10px}

/* footer */
.site-footer{position:absolute;top:2692px;left:0;width:1200px;height:333px;background:var(--light);color:var(--ink)}
.site-footer .wordmark{position:absolute;left:80px;top:48px;font-size:46px}
.copyright{position:absolute;left:78px;top:150px;font-size:13px}
.site-footer .social{left:77px;top:210px}
.site-footer h3{font-size:15px;font-weight:700;letter-spacing:.3px}
.quick-links{position:absolute;left:480px;top:56px}
.quick-links ul{list-style:none;margin-top:20px}
.quick-links li{font-size:15px;line-height:33.5px;padding-left:20px;position:relative}
.quick-links li::before{content:"";position:absolute;left:0;top:13px;border-left:5px solid var(--ink);border-top:4px solid transparent;border-bottom:4px solid transparent}
.contact{position:absolute;left:880px;top:48px;width:250px}
.contact .company{font-size:17px;margin-top:20px}
.contact ul{list-style:none;margin-top:18px}
.contact li{position:relative;padding-left:29px;font-size:14px;line-height:18px;margin-bottom:13px;white-space:nowrap}
.contact li svg{position:absolute;left:0;top:2px}
.site-code{position:absolute;left:1140px;top:272px;font-size:13px}
</style>
</head>
<body>

<header class="site-header">
  <div class="wordmark">VEDRANA</div>
  <div class="social" aria-label="Social links">
    <span class="dot"></span><span class="dot"></span><span class="dot"></span><span class="dot"></span><span class="dot"></span>
  </div>
  <div class="call">
    <div class="call-icon">
      <svg width="16" height="16" viewBox="0 0 24 24"><path fill="#fff" d="M6.6 10.8a15 15 0 0 0 6.6 6.6l2.2-2.2c.3-.3.7-.4 1-.2 1.1.4 2.3.6 3.6.6.6 0 1 .4 1 1V20c0 .6-.4 1-1 1A17 17 0 0 1 3 4c0-.6.4-1 1-1h3.5c.6 0 1 .4 1 1 0 1.3.2 2.5.6 3.6.1.3 0 .7-.2 1z"/></svg>
    </div>
    <div><small>Call Us Now</small><strong>0555 01234</strong></div>
  </div>
</header>

<nav class="main-nav">
  <a class="active" href="#">HOME</a>
  <a href="#">ABOUT US</a>
  <a href="#">FULL MOTION CRAFT</a>
  <a href="#">MORE...</a>
</nav>

<section class="hero" role="img" aria-label="Close-up photograph of green twisted yarn strands">
  <h1>TAILORED WEAVING SOLUTIONS</h1>
  <div class="badge"><span>40</span><em>Vedrana</em></div>
  <svg class="hero-arrows" width="76" height="40" viewBox="0 0 76 40"><path d="M20 4 6 20l14 16M56 4l14 16-14 16" fill="none" stroke="rgba(255,255,255,.6)" stroke-width="2"/></svg>
</section>

<section class="features">
  <article class="feature">
    <svg width="42" height="40" viewBox="0 0 24 23"><path fill="#fff" d="M12 0l3.5 7.3 8 1.1-5.8 5.6 1.4 8L12 18.2 4.9 22l1.4-8L.5 8.4l8-1.1z"/></svg>
    <h2>Experience</h2>
    <p>Over the years the company has gained the knowledge and skills that define the superiority of our product and the rigor of our work ethic</p>
    <a class="btn btn-white" style="top:265px" href="#">Read more</a>
  </article>
  <article class="feature">
    <svg width="44" height="40" viewBox="0 0 24 22"><path fill="#fff" d="M22 1C12 1 4 5 4 14c0 1.5.3 3 1 4.2L2 21l1 1 3.2-2.8c1.3.6 2.8.9 4.3.9C19 20 22 11 22 1zM8 17c2-5 6-8 10-10-4 3-7 6-9 11z"/></svg>
    <h2>Creativity</h2>
    <p>Our belief is that the key to our clients' success is a combination of innovation, creativity and quality.<br>We strive to adapt and re-imagine our product, implementing these principles in order to meet and exceed our clients' demands (every time)</p>
    <a class="btn btn-white" style="top:320px" href="#">Read more</a>
  </article>
  <article class="feature">
    <svg width="50" height="40" viewBox="0 0 30 22"><g fill="#fff"><circle cx="15" cy="5" r="4"/><circle cx="6" cy="7" r="3"/><circle cx="24" cy="7" r="3"/><path d="M8 20c0-5 3-8 7-8s7 3 7 8z"/><path d="M0 20c0-4 2-7 6-7 1.5 0 2.5.4 3 1-1.5 1.5-2.5 3.5-2.5 6zM30 20c0-4-2-7-6-7-1.5 0-2.5.4-3 1 1.5 1.5 2.5 3.5 2.5 6z"/></g></svg>
    <h2>Professionality</h2>
    <p>We are a family business at the core. Our company is run with the same values as the Ferrante family: respect, determination and commitment.</p>
    <a class="btn btn-white" style="top:265px" href="#">Read more</a>
  </article>
</section>

<section class="approach">
  <h2 class="section-title">PRODUCTION BUILT AROUND YOU</h2>
  <div class="concept-mark" role="img" aria-label="Full Motion Craft concept mark"></div>
  <p class="lead">Versatility and flexibility both in development and production are key in delivering a custom<br>solution capable of giving life to your products.</p>
  <a class="btn btn-green" href="#">Find Out More</a>
</section>

<section class="team" role="img" aria-label="Soft background photograph of yellow and pink yarn balls">
  <p class="p1">Our team has decades of experience in providing yarn solutions to weavers around the world, assisting<br>them in the creation of outstanding textiles.</p>
  <p class="p2">Our clients can expect open lines of communication, clarity and professionality</p>
  <p class="p3">Our focus is our client.<br>The success of a client is our success.</p>
  <a class="btn btn-green" href="#">OUR HERITAGE</a>
</section>

<section class="numbers" role="img" aria-label="Faded photograph of woven fabric with yellow thread">
  <h2 class="section-title">VDR IN NUMBERS</h2>
  <div class="stats">
    <div class="stat"><b>40</b><span>YEARS IN BUSINESS</span></div>
    <div class="stat"><b>2</b><span>MILLION KILOGRAMS/ YR</span></div>
    <div class="stat"><b>8</b><span>BRANDS</span></div>
  </div>
  <a class="btn btn-green" href="#">Find out more</a>
</section>

<section class="testimonials" role="img" aria-label="Dark photograph of yarn spinning machinery">
  <h2 class="section-title">TESTIMONIALS</h2>
  <div class="quote-mark">&rdquo;</div>
  <p>Urna vestibulum placerat nulla velit sed a malesuada sollicitudin dolor mi quam a sit quis diam orci blandit. Nec dolor ipsum proin ipsum suscipit. Vitae mauris mi. Sed magna magnis in natoque</p>
  <cite>- Marta</cite>
</section>

<footer class="site-footer">
  <div class="wordmark">VEDRANA</div>
  <p class="copyright">&copy; 2018 &nbsp;| ALL RIGHTS RESERVED.</p>
  <div class="social" aria-label="Social links">
    <span class="dot"></span><span class="dot"></span><span class="dot"></span><span class="dot"></span><span class="dot"></span>
  </div>
  <div class="quick-links">
    <h3>QUICK LINKS</h3>
    <ul>
      <li>Home</li>
      <li>About Us</li>
      <li>Full Motion Craft</li>
      <li>MORE...</li>
    </ul>
  </div>
  <div class="contact">
    <h3>CONTACT US</h3>
    <p class="company">Vedrana Novelty Yarn Solutions</p>
    <ul>
      <li><svg width="14" height="16" viewBox="0 0 24 28"><path fill="#1d1d1d" d="M12 0a9 9 0 0 0-9 9c0 7 9 19 9 19s9-12 9-19a9 9 0 0 0-9-9zm0 12.5A3.5 3.5 0 1 1 12 5.5a3.5 3.5 0 0 1 0 7z"/></svg>Tessora s.r.l<br>Via dei Telai<br>12 - 50100 Borgo Lana - Italy.</li>
      <li><svg width="13" height="13" viewBox="0 0 24 24"><path fill="#1d1d1d" d="M6.6 10.8a15 15 0 0 0 6.6 6.6l2.2-2.2c.3-.3.7-.4 1-.2 1.1.4 2.3.6 3.6.6.6 0 1 .4 1 1V20c0 .6-.4 1-1 1A17 17 0 0 1 3 4c0-.6.4-1 1-1h3.5c.6 0 1 .4 1 1 0 1.3.2 2.5.6 3.6.1.3 0 .7-.2 1z"/></svg>0555 01234</li>
      <li><svg width="14" height="13" viewBox="0 0 24 22"><path fill="#1d1d1d" d="M5 0h11v6H5zM2 8h20v12H2zm4 3v2h4v-2zm0 4v2h4v-2zm6-4v2h4v-2z"/></svg>0555 09876</li>
      <li><svg width="14" height="11" viewBox="0 0 24 18"><path fill="#1d1d1d" d="M0 0h24v3l-12 7L0 3zm0 6 12 7 12-7v12H0z"/></svg>hello@vedranathreads.example</li>
    </ul>
  </div>
  <span class="site-code">M1</span>
</footer>

</body>
</html>
```